Business Card Design

I already have a company logo for my company. I have a logo for the manufacturer we represent. I want a professional business card design.

```html
<!DOCTYPE html>
<html lang="en">
<head>
<meta charset="utf-8">
<title>Signal Works LLC – Business Card</title>
<link href="https://fonts.googleapis.com/css2?family=Open+Sans:wght@400;600;700;800&display=swap" rel="stylesheet">
<style>
  :root {
    --stage: #242424;
    --card-dark: #1f1f22;
    --brand-red: #e31e2d;
    --brand-red-deep: #c8141f;
    --brand-orange: #f26a2e;
    --brand-gold: #d4a12a;
    --ink-light: #ffffff;
    --ink-soft: #e8e8e8;
  }
  * { box-sizing: border-box; margin: 0; padding: 0; }
  html, body {
    width: 1200px; height: 780px; overflow: hidden;
    background: var(--stage);
    font-family: "Open Sans", Arial, sans-serif;
  }
  .stage {
    width: 1200px; height: 780px;
    display: flex; align-items: center; justify-content: center; gap: 40px;
  }
  .card {
    width: 540px; height: 309px;
    position: relative; overflow: hidden;
    box-shadow: 0 14px 30px rgba(0,0,0,.45);
  }

  /* Back side */
  .card--back {
    background: var(--brand-red);
  }
  .card-back__pattern {
    position: absolute; inset: 0;
    background: linear-gradient(160deg, var(--brand-orange) 0%, var(--brand-red) 45%, var(--brand-red-deep) 100%);
    opacity: .9;
  }
  .card-back__mark {
    position: absolute; right: 26px; bottom: 22px;
    display: flex; align-items: center; gap: 6px;
    font-weight: 700; font-size: 10px; letter-spacing: .06em;
    color: var(--ink-light); text-transform: uppercase;
  }
  .card-back__mark .dot {
    width: 9px; height: 9px; background: var(--ink-light);
  }

  /* Front side */
  .card--front {
    background: var(--card-dark);
    border-bottom: 4px solid var(--brand-red);
    display: flex; align-items: center;
  }
  .brand {
    width: 250px; height: 100%;
    display: flex; align-items: center; justify-content: center; gap: 10px;
  }
  .brand__square {
    width: 26px; height: 26px; background: var(--brand-red); flex: none;
  }
  .brand__name {
    font-weight: 800; font-size: 22px; line-height: 1.1;
    color: var(--ink-light); text-transform: uppercase; letter-spacing: .02em;
  }
  .divider {
    width: 2px; height: 170px; background: var(--ink-light); flex: none;
  }
  .contact {
    padding-left: 30px; color: var(--ink-light);
  }
  .contact__name {
    font-weight: 800; font-size: 27px; line-height: 1.05; letter-spacing: -.01em;
  }
  .contact__first { color: var(--brand-red); }
  .contact__last { color: var(--brand-gold); }
  .contact__title {
    font-weight: 600; font-size: 13px; margin-top: 2px;
  }
  .contact__address {
    font-size: 12.5px; line-height: 1.45; margin-top: 16px; color: var(--ink-soft);
  }
  .contact__list {
    list-style: none; margin-top: 12px;
    font-size: 12.5px; line-height: 1.7; color: var(--ink-soft);
  }
  .contact__list li { display: flex; align-items: center; gap: 8px; }
  .contact__list svg { width: 12px; height: 12px; fill: var(--brand-red); flex: none; }
</style>
</head>
<body>
<main class="stage">

  <section class="card card--back" aria-label="Business card, back">
    <div class="card-back__pattern" role="img" aria-label="Repeating brand symbol pattern in red and orange tones"></div>
    <div class="card-back__mark"><span class="dot"></span>Signal Works LLC</div>
  </section>

  <section class="card card--front" aria-label="Business card, front">
    <div class="brand">
      <span class="brand__square"></span>
      <span class="brand__name">Signal Works<br>LLC</span>
    </div>
    <div class="divider"></div>
    <div class="contact">
      <h1 class="contact__name"><span class="contact__first">Tomas</span> <span class="contact__last">Kralik</span></h1>
      <p class="contact__title">Managing Director</p>
      <p class="contact__address">1840 Meadow Ln. Suite 310<br>Arlington, TX 76010</p>
      <ul class="contact__list">
        <li>
          <svg viewBox="0 0 24 24" aria-hidden="true"><path d="M6.6 10.8a15.1 15.1 0 0 0 6.6 6.6l2.2-2.2a1 1 0 0 1 1-.25 11.4 11.4 0 0 0 3.6.57 1 1 0 0 1 1 1V20a1 1 0 0 1-1 1A17 17 0 0 1 3 4a1 1 0 0 1 1-1h3.5a1 1 0 0 1 1 1c0 1.25.2 2.45.57 3.6a1 1 0 0 1-.25 1z"/></svg>
          (555) 214-6630
        </li>
        <li>
          <svg viewBox="0 0 24 24" aria-hidden="true"><path d="M2 5h20v14H2zm2 2v.5l8 5 8-5V7zm0 2.8V17h16V9.8l-8 5z"/></svg>
          info@website.com
        </li>
        <li>
          <svg viewBox="0 0 24 24" aria-hidden="true"><path d="M12 2a10 10 0 1 0 0 20 10 10 0 0 0 0-20zm6.9 6h-3a15.6 15.6 0 0 0-1.4-3.6A8 8 0 0 1 18.9 8zM12 4a14 14 0 0 1 1.9 4h-3.8A14 14 0 0 1 12 4zM4.3 14a8 8 0 0 1 0-4h3.4a16 16 0 0 0 0 4zm.8 2h3a15.6 15.6 0 0 0 1.4 3.6A8 8 0 0 1 5.1 16zm3-8h-3a8 8 0 0 1 4.4-3.6A15.6 15.6 0 0 0 8.1 8zM12 20a14 14 0 0 1-1.9-4h3.8A14 14 0 0 1 12 20zm2.3-6H9.7a14.7 14.7 0 0 1 0-4h4.6a14.7 14.7 0 0 1 0 4zm.2 5.6a15.6 15.6 0 0 0 1.4-3.6h3a8 8 0 0 1-4.4 3.6zm1.8-5.6a16 16 0 0 0 0-4h3.4a8 8 0 0 1 0 4z"/></svg>
          www.website.com
        </li>
      </ul>
    </div>
  </section>

</main>
</body>
</html>
```